Business Card Design For Office Furniture Clearance Company

Kestrel Office Clearance - our company name pretty much explains what we do, we clear offices for high end clients, mainly plc's and large international companies.

We require a nice looking business card that displays professionalism but without being too serious.

It would be nice to see just a little more than a conventional boring business card, make sure you add some flare.

Industry/Entity Type

Office Furniture

Contact Information for Business Card

CARD 1

Mark Holloway
Director
mark@kestrelofficeclearance.co.uk
m: 07700 153928

t: 01632 960418
www.kestrelofficeclearance.co.uk

Kestrel Office Clearance
Unit K4 B
2-8 Fenwick Lane
Harwick
Northbridge
ZZ9 4QT

free office clearances… you cant get better than that.

CARD 2

Peter Radford
Director
peter@kestrelofficeclearance.co.uk
m: 07700 382615

t: 01632 960418

Kestrel Office Clearance
Unit K4 B
2-8 Fenwick Lane
Harwick
Northbridge
ZZ9 4QT

Font styles to use
Sans Serif

Requirements
Must have
• A white background - as we have a blue logo.
Nice to have
• Nice use of the logo - play around with this and dissect it.

```html
<!DOCTYPE html>
<html lang="en">
<head>
<meta charset="utf-8">
<title>Kestrel Office Clearance – Business Card</title>
<link rel="stylesheet" href="https://fonts.googleapis.com/css2?family=Source+Sans+3:wght@400;600;700&display=swap">
<style>
  :root {
    --stage: #1c1c1c;
    --card-front: #f3f3f3;
    --brand-blue: #0a6fb3;
    --brand-blue-top: #0079bd;
    --brand-blue-bottom: #005c94;
    --name-blue: #1567a8;
    --ink: #1d1d1d;
    --white: #ffffff;
  }
  * { margin: 0; padding: 0; box-sizing: border-box; }
  html, body {
    width: 1200px; height: 900px; overflow: hidden;
    background: var(--stage);
    font-family: "Source Sans 3", Arial, sans-serif;
  }
  .canvas { position: relative; width: 1200px; height: 900px; }

  .card {
    position: absolute; top: 184px; height: 490px; border-radius: 14px; overflow: hidden;
  }
  .card--front { left: 299px; width: 301px; background: var(--card-front); }
  .card--back {
    left: 645px; width: 304px;
    background: linear-gradient(180deg, var(--brand-blue-top) 0%, var(--brand-blue-bottom) 100%);
  }

  .brand-mark {
    position: absolute; border-radius: 50%;
    display: flex; align-items: center; justify-content: center;
    font-weight: 700; letter-spacing: 1px; font-size: 24px;
  }
  .card--front .brand-mark {
    left: 71px; top: 41px; width: 160px; height: 160px;
    background: var(--brand-blue); color: var(--white);
  }
  .card--back .brand-mark {
    left: 69px; top: 216px; width: 166px; height: 166px;
    background: var(--white); color: var(--brand-blue);
  }

  .person { position: absolute; top: 251px; width: 100%; text-align: center; }
  .person__name { font-size: 19px; font-weight: 600; color: var(--name-blue); line-height: 24px; }
  .person__role { font-size: 13.5px; color: var(--ink); line-height: 18px; }

  .contact-list {
    position: absolute; top: 310px; width: 100%; list-style: none;
    display: flex; flex-direction: column; align-items: center;
  }
  .contact-list li {
    font-size: 14px; color: var(--ink); line-height: 20.5px;
    display: flex; align-items: center; gap: 4px;
  }
  .contact-list svg { width: 10px; height: 10px; fill: var(--name-blue); flex: none; }

  .company { position: absolute; top: 411px; width: 100%; text-align: center; }
  .company__name { font-size: 17.5px; font-weight: 600; color: var(--name-blue); line-height: 22px; }
  .company__address { font-size: 14px; color: var(--ink); line-height: 19px; }

  .tagline {
    position: absolute; top: 407px; width: 100%; text-align: center;
    color: var(--white); font-weight: 700; font-size: 16px; line-height: 20px;
    text-transform: uppercase;
  }
</style>
</head>
<body>
<main class="canvas">
  <section class="card card--front" aria-label="Card front">
    <div class="brand-mark">KESTREL</div>

    <div class="person">
      <p class="person__name">Mark Holloway</p>
      <p class="person__role">Director</p>
    </div>

    <ul class="contact-list">
      <li>
        <svg viewBox="0 0 10 10" aria-hidden="true"><path d="M2.5 0h5a1 1 0 0 1 1 1v8a1 1 0 0 1-1 1h-5a1 1 0 0 1-1-1V1a1 1 0 0 1 1-1zm.3 1.2v6.3h4.4V1.2zM5 8.1a.5.5 0 1 0 0 1 .5.5 0 0 0 0-1z"/></svg>
        07700 153928
      </li>
      <li>
        <svg viewBox="0 0 10 10" aria-hidden="true"><path d="M2.2.3l1.5 1.8-.8 1.2a6 6 0 0 0 3.8 3.8l1.2-.8 1.8 1.5-.9 1.6C4.5 9.4.6 5.5.6 1.2z"/></svg>
        01632 960418
      </li>
      <li>
        <svg viewBox="0 0 10 10" aria-hidden="true"><path d="M0 2h10v6H0zm.8.6L5 5.6l4.2-3z"/></svg>
        mark@kestrelofficeclearance.co.uk
      </li>
      <li>
        <svg viewBox="0 0 10 10" aria-hidden="true"><circle cx="5" cy="5" r="5"/><path d="M2 3.5c1 .3 1.5 1 1.2 2l1 1.2-.3 2M6 1.2c-.2 1 .5 1.4 1.5 1.5l.3 1.8L6.5 6" stroke="#f3f3f3" stroke-width=".8" fill="none"/></svg>
        www.kestrelofficeclearance.co.uk
      </li>
    </ul>

    <div class="company">
      <p class="company__name">Kestrel Office Clearance</p>
      <p class="company__address">Unit K4 B, 2-8 Fenwick Lane<br>Harwick, Northbridge&nbsp; ZZ9 4QT</p>
    </div>
  </section>

  <section class="card card--back" aria-label="Card back">
    <div class="brand-mark">KESTREL</div>
    <p class="tagline">Free office clearances…<br>You cant get better than that</p>
  </section>
</main>
</body>
</html>
```